Plumbing company needs Business Card Design

Hi I need business card design based on logo which I uploaded. Its plumbing and heating company called Kranex Usługi Hydrauliczno-Gazowe. I want to see on my card motto of my company which is "...od wymiany uszczelki po wymiane łazienki.", my phone number, name, and website: 612478390, Marek Olejnik, info@kranex-inst.org, www.kranex-inst.org
I want to see logos of companys which I'm approved installer (Termova) (Le Valmont) (Korvo) (Plumox).
I want new creative look of business card. I like rounded corners.
Any questions please send message.
Thanks for intrest.
Industry/Entity Type
Business
Contact Information for Business Card
Marek Olejnik
612 478 390
info@kranex-inst.org
www.kranex-inst.org
...od wymiany uszczelki po wymiane łazienki.

```html
<!DOCTYPE html>
<html lang="pl">
<head>
<meta charset="utf-8">
<title>Kranex – wizytówka</title>
<link rel="stylesheet" href="https://fonts.googleapis.com/css2?family=Open+Sans:wght@400;600;800&family=Roboto+Condensed:wght@700&display=swap">
<style>
  :root {
    --stage: #4b4b4b;
    --red: #e31e24;
    --yellow: #f6ec1c;
    --navy: #1f3f8a;
    --ink: #1a1a1a;
    --white: #ffffff;
  }
  * { box-sizing: border-box; margin: 0; padding: 0; }
  html, body { width: 1200px; height: 900px; overflow: hidden; }
  body {
    background: var(--stage);
    font-family: "Open Sans", Arial, sans-serif;
    position: relative;
  }
  .card {
    position: absolute;
    top: 250px;
    width: 400px;
    height: 400px;
    border-radius: 44px;
    overflow: hidden;
  }
  /* Front */
  .card-front { left: 160px; background: var(--red); }
  .front-panel {
    position: absolute;
    inset: 20px;
    background: var(--yellow);
    border-radius: 32px;
  }
  .front-illustration {
    position: absolute;
    left: 50px; top: 38px;
    width: 260px; height: 284px;
    border-radius: 120px 120px 20px 20px;
    background: radial-gradient(circle at 50% 40%, #2a4c98, var(--navy));
  }
  /* Back */
  .card-back { left: 640px; background: var(--white); }
  .back-topline {
    position: absolute; left: 0; right: 0; top: 0; height: 10px;
    background: var(--red);
  }
  .brand { position: absolute; left: 30px; top: 50px; display: flex; align-items: center; gap: 14px; }
  .brand-square {
    width: 100px; height: 100px; border-radius: 14px;
    background: var(--yellow); border: 6px solid var(--red);
  }
  .brand-text { display: flex; flex-direction: column; }
  .brand-name {
    font-weight: 800; font-size: 50px; line-height: 1; color: var(--red);
  }
  .brand-tagline {
    margin-top: 6px;
    font-family: "Roboto Condensed", Arial, sans-serif;
    font-size: 17px; color: var(--navy);
  }
  .motto {
    position: absolute; left: 0; right: 0; top: 172px;
    text-align: center; color: var(--red);
    font-size: 16px; line-height: 22px;
  }
  .contact-band { position: absolute; left: 0; top: 222px; width: 400px; height: 112px; }
  .person {
    position: absolute; left: 40px; top: 250px;
    font-size: 24px; line-height: 30px;
  }
  .person-first { color: var(--ink); }
  .person-last { color: var(--navy); font-weight: 600; font-size: 22px; }
  .divider { position: absolute; left: 196px; top: 248px; width: 2px; height: 72px; background: var(--red); }
  .contacts { position: absolute; left: 210px; top: 254px; font-size: 16px; line-height: 28px; color: var(--ink); list-style: none; }
  .contacts li { display: flex; align-items: center; gap: 6px; }
  .contacts svg { width: 12px; height: 12px; fill: var(--navy); }
  .website {
    position: absolute; left: 0; right: 0; top: 354px;
    text-align: center; color: var(--navy); font-weight: 600; font-size: 18px;
  }
  .back-bottomline {
    position: absolute; left: 0; right: 0; bottom: 0; height: 8px;
    background: var(--red);
  }
</style>
</head>
<body>
  <section class="card card-front">
    <div class="front-panel">
      <div class="front-illustration" role="img" aria-label="Illustration of a plumber in a cap holding a plunger and a wrench"></div>
    </div>
  </section>

  <section class="card card-back">
    <div class="back-topline"></div>
    <div class="brand">
      <div class="brand-square"></div>
      <div class="brand-text">
        <span class="brand-name">Kranex</span>
        <span class="brand-tagline">Usługi Hydrauliczno-Gazowe</span>
      </div>
    </div>
    <p class="motto">Od wymiany uszczelki<br>po wymiane łazienki</p>

    <svg class="contact-band" viewBox="0 0 400 112" aria-hidden="true">
      <rect x="0" y="0" width="400" height="112" fill="#f6ec1c"/>
      <polygon points="0,0 40,0 22,86 180,112 0,112" fill="#e31e24"/>
    </svg>
    <div class="person">
      <div class="person-first">Marek</div>
      <div class="person-last">Olejnik</div>
    </div>
    <div class="divider"></div>
    <ul class="contacts">
      <li><svg viewBox="0 0 12 12"><path d="M2 1l2 0 1 3-1.5 1a7 7 0 0 0 3.5 3.5L8 7l3 1v2c0 1-1 1.5-2 1.5A9 9 0 0 1 .5 3C.5 2 1 1 2 1z"/></svg>612.478.390</li>
      <li><svg viewBox="0 0 12 12"><rect x="0" y="3" width="12" height="7"/></svg>info@kranex-inst.org</li>
    </ul>
    <div class="website">www.kranex-inst.org</div>
    <div class="back-bottomline"></div>
  </section>
</body>
</html>
```